Cannabis Media Network Advertising Kit

Polar Orbit Media is a digital media news network focused on the startups, entrepreneurs and innovative companies in the cannabis industry. We are ready to release our new services for 2017.

We are looking for a modern looking advertising kit created that we would send to our potential clients.

We want it to look similar to our branding. Our website is www.polarorbitmedia.example.

Target Market(s)

Page 3: Audience:
Entrepreneurs, professionals, execs, VC’s, and Investors
Include stats: 34% Female/ 66% Male, 34% 25-34 Years Old $24% 35-44 Years Old

Industry/Entity Type

Media

Font styles to use
Sans Serif

Colors
0555a3
0492cd
ffffff
edf1f7

Requirements
Must have
• Outline Idea is below. Images can be provided.
• Page 1: Header Page (POM logo)
• Leading digital media news network covering the latest tech, startups, and innovative companies in the cannabis industry.
• Page 2: About Us - Mission and Brand
• Polar Orbit Media is the leading digital media platform that is dedicated to profiling the startups, entrepreneurs and innovative companies in the cannabis industry.
• Over the past few years we have been highlighting the upcoming and established businesses in the industry, developed a platform for leaders to share their knowledge and insight, and created
• a spotlight for the innovative technology.
• But most importantly, we have created a community of entrepreneurs, investors and professionals who have the same mission of growing the b2b industry together.
• POM is more than just a network and brand, we are highlighting history in the making of high quality original content.
• Page 3: Audience:
• Entrepreneurs, professionals, execs, VC’s, and Investors
• Include stats: 34% Female/ 66% Male, 34% 25-34 Years Old $24% 35-44 Years Old
• Page 4: POM Original Web Series
• Pre/Post Commercial Opportunities $5,000
• Tinbell Reviews and POM Talks
• Tinbell Reviews is a un-biased product review segment for the wholesalers, online stores, dispensaries and more.
• POM Talks: One on one interview with the upcoming and leading founders offering advice and insight for fellow entrepreneurs.
• Page 5: POM Original Web Series
• Kettles and Kites is a female founder focused web series, where we highlight the leaders, discuss informative topics and latest products.
• Product placement $2,500
• Page 6: POM Original Web Series
• Upside Ledge gives you a peek into the entrepreneur 2.0 and what it is like running a cannabis business.
• See leadership package
• Page 7: Package 1: Foundation $1,000
• 1. Four full platform ads (via QT, ZR, Plonkit, Fernwork, Braxtile)
• 2. POM Article/Company Spotlight (One Newsletter feature and full POM promotion)
• 3. Newsletter Ad (One run, assets provided by client
• Page 8: Package 2: Traction $5,000
• 1. Six full platform ads (via QT, ZR, Plonkit, Fernwork, Braxtile)
• 4. Business of the Month Badge (POM Homepage)
• 5. Three Verbal Video Advertisements ( Three segments, up to 10 seconds each)
• Page 9: Package 3: Leadership $15,000
• 5. Three Video Advertisements (Three segments, 30 second commercial)
• 7. Upside Ledge Full Segment
• Includes promo and full segment promoted and released via POM.
• Page 10: Events Promotion
• Event Package $1,000
• 1. Four full platform ads (via QT include QT Event on POM Page, ZR, Plonkit, Fernwork, Braxtile)
• A la Carte:
• Add event to POM calendar, basic promotion via social media $250
• POMTV Media Sponsor
• Includes co-branded video production of event, exclusive interview with sponsors, and more
• *Cost: To Be Determined
• Page 11: A La Carte
• 1. Event Addition to Calendar (Basic promotion via social media)
• 2. Six full platform ads (via QT, ZR, Plonkit, Fernwork, Braxtile)
• 3. POM Article/Company Spotlight (One Newsletter feature and full POM promotion)
• 4. Newsletter Ad (One run, assets provided by client
• 5. Business of the Month Badge (POM Homepage)
• 6. Three Verbal Video Advertisements ( Three segments, up to 10 seconds each)
• Page 12: Traction
• Profiled on fernwork, orbel daily, spindara, quillstoa, plonkit, zephrame
• 10k+ organic email list of professionals
• 16k+ page views increasing 25% each month
• 18k+ social media followers
• Viewed in all 50 states and 98 countries
• Page 13: Message from the CEO
• “We at POM understand that our industry is different than any other industry out there, we even look at the entrepreneurs and don’t see them just as an entrepreneur but as an entrepreneur 2.0. Why? Because this is the first time in a long time where we have the opportunity to change how an industry is built from the foundation up and each of these individuals are faced with hurdles and challenges we wouldn’t face in any other industry and yet they are doing what it takes to continue to move forward.”
• Page 14: Contact Us
• POM logo:
• We look forward to growing your brand with the Polar Orbit Media! Contact us today at contact@polarorbitmedia.example
Nice to have
• High Res Images from our content. Which we can provide those images, or you can pull from our site and we can send high res after.
Should not have
• Dark Designed.

```html
<!DOCTYPE html>
<html lang="en">
<head>
<meta charset="utf-8">
<title>Polar Orbit Media — Audience</title>
<link rel="stylesheet" href="https://fonts.googleapis.com/css2?family=Open+Sans:wght@400;600;700&family=Ubuntu:wght@500;700&display=swap">
<style>
  :root {
    --brand-blue: #0555a3;
    --brand-sky: #0492cd;
    --brand-white: #ffffff;
    --page-bg: #edf1f7;
    --female: #6455a6;
    --male: #f26a21;
    --age-young: #05a4c0;
    --age-mid: #0555a3;
    --age-rest: #d1d3d6;
    --facet-light: #4aa3e0;
    --facet-dark: #1368bd;
  }
  html, body { margin: 0; padding: 0; overflow: hidden; }
  body { width: 1200px; height: 900px; background: var(--page-bg); }
  .slide {
    position: relative; width: 1200px; height: 900px; overflow: hidden;
    background: var(--page-bg);
    font-family: "Open Sans", Arial, sans-serif;
  }
  .slide-art { position: absolute; inset: 0; }
  .section-title {
    position: absolute; left: 52px; top: 190px; width: 200px; text-align: center;
    font-family: "Ubuntu", "Open Sans", sans-serif; font-weight: 700;
    font-size: 26px; color: var(--brand-blue); letter-spacing: 0.2px;
  }
  .audience-heading {
    position: absolute; left: 480px; top: 166px; margin: 0;
    font-weight: 400; font-size: 32px; line-height: 39px; color: var(--brand-sky);
  }
  .stats-intro {
    position: absolute; left: 480px; top: 298px; margin: 0;
    font-weight: 400; font-size: 32px; color: var(--brand-sky);
  }
  .stat { position: absolute; text-align: center; width: 160px; }
  .stat-value { display: block; font-weight: 700; font-size: 36px; line-height: 38px; }
  .stat-label { display: block; font-weight: 700; font-size: 18px; line-height: 22px; }
  .stat--female { left: 495px; top: 574px; color: var(--female); }
  .stat--male   { left: 495px; top: 668px; color: var(--male); }
  .stat--young  { left: 771px; top: 574px; color: var(--age-young); }
  .stat--mid    { left: 771px; top: 668px; color: var(--age-mid); }
  .brand-mark {
    position: absolute; left: 1092px; top: 804px;
    font-weight: 700; font-size: 22px; color: var(--brand-blue);
  }
  .page-number {
    position: absolute; left: 1148px; top: 846px;
    font-size: 18px; color: #555b66;
  }
</style>
</head>
<body>
<main class="slide">
  <svg class="slide-art" width="1200" height="900" viewBox="0 0 1200 900" aria-hidden="false">
    <defs>
      <linearGradient id="facetFill" x1="0" y1="0" x2="1" y2="1">
        <stop offset="0" stop-color="var(--facet-light)"/>
        <stop offset="0.5" stop-color="#2a86d3"/>
        <stop offset="1" stop-color="var(--facet-dark)"/>
      </linearGradient>
    </defs>

    <!-- corner panel -->
    <polygon class="corner-panel" points="0,0 275,0 0,400" fill="url(#facetFill)" role="img" aria-label="Faceted blue geometric background texture"/>
    <line class="corner-rule" x1="292" y1="0" x2="0" y2="424" stroke="var(--brand-sky)" stroke-width="4"/>

    <!-- section badge -->
    <circle cx="152" cy="205" r="149" fill="var(--brand-white)"/>
    <circle cx="152" cy="205" r="138" fill="url(#facetFill)"/>
    <circle cx="152" cy="205" r="102" fill="var(--brand-white)"/>

    <!-- gender pie -->
    <g class="pie pie--gender" transform="translate(485,362)">
      <path d="M89,89 L89,0 A89,89 0 1 1 13.86,136.7 Z" fill="var(--male)"/>
      <path d="M89,89 L89,0 A89,89 0 0 0 13.86,136.7 Z" fill="var(--female)"/>
    </g>

    <!-- age pie -->
    <g class="pie pie--age" transform="translate(761,362)">
      <path d="M89,89 L89,0 A89,89 0 0 1 177.8,83.4 Z" fill="var(--age-mid)"/>
      <path d="M89,89 L177.8,83.4 A89,89 0 0 1 13.86,136.7 Z" fill="var(--age-rest)"/>
      <path d="M89,89 L89,0 A89,89 0 0 0 13.86,136.7 Z" fill="var(--age-young)"/>
    </g>

    <!-- person icons -->
    <g class="icon icon--female" fill="none" stroke="var(--female)" stroke-width="1.8">
      <circle cx="490" cy="606" r="22"/>
      <ellipse cx="490" cy="600" rx="7" ry="8.5"/>
      <path d="M476,622 C478,613 484,611 490,611 C496,611 502,613 504,622"/>
    </g>
    <g class="icon icon--male" fill="none" stroke="var(--male)" stroke-width="1.8">
      <circle cx="490" cy="700" r="22"/>
      <ellipse cx="490" cy="694" rx="7" ry="8.5"/>
      <path d="M476,716 C478,707 484,705 490,705 C496,705 502,707 504,716"/>
    </g>

    <!-- legend keys -->
    <rect x="746" y="599" width="15" height="15" fill="var(--age-young)"/>
    <rect x="746" y="693" width="15" height="15" fill="var(--age-mid)"/>

    <!-- footer rules -->
    <line x1="1205" y1="708" x2="1092" y2="905" stroke="var(--brand-sky)" stroke-width="4"/>
    <line x1="1205" y1="758" x2="1122" y2="905" stroke="var(--brand-sky)" stroke-width="4"/>
  </svg>

  <div class="section-title">AUDIENCE</div>

  <h2 class="audience-heading">Entrepreneurs, professionals,<br>execs, VC’s, and Investors</h2>
  <p class="stats-intro">• Include stats:</p>

  <div class="stat stat--female"><span class="stat-value">34%</span><span class="stat-label">Female</span></div>
  <div class="stat stat--male"><span class="stat-value">66%</span><span class="stat-label">Male</span></div>
  <div class="stat stat--young"><span class="stat-value">34%</span><span class="stat-label">25-34 Years Old</span></div>
  <div class="stat stat--mid"><span class="stat-value">24%</span><span class="stat-label">35-44 Years Old</span></div>

  <div class="brand-mark">POM</div>
  <div class="page-number">3</div>
</main>
</body>
</html>
```